Business Card for Beach theme sports bar called MORVIN

I need a business card designed for our employees, front and back. This will be used by the employees of two business locations to hand out to customers. I've attached the previous business cards we used at one time for a Dantells (it is now Morvin). Looking for a fresh new card that is elegant but has character.

Target Market(s)

30-60, middle class

Contact Information for Business Card

We are a beach bar and sports bar. I am looking for an elegant business card with the front to have the MORVIN logo. Then on the back I need it to allow a space for employees to write their names and for them to write in their schedule. I have attached our old cards with our old name Dantells so you can pull everything we need on the cards. one thing is missing is we have another location at 2615 W Calder Ridge Rd with a number of 702-418-9053. Since we will use it for both locations it should allow the employee to circle or check mark the bar which they work at.

Font styles to use
Sans Serif

Requirements
Must have
• We are looking for some fresh ideas for the business card. Something that will really stick out to customers when the staff hands them out. Creativity will be looked at positively, but we still want it to look upscale and fun.

```html
<!DOCTYPE html>
<html lang="en">
<head>
<meta charset="utf-8">
<title>Morvin Business Card</title>
<link rel="stylesheet" href="https://fonts.googleapis.com/css2?family=Work+Sans:wght@400;500;600&display=swap">
<style>
  :root {
    --stage: #2a2a2a;
    --card-dark: #121212;
    --card-light: #ffffff;
    --ink: #1c1c1c;
    --muted: #6a6a6a;
    --rule: #2b2b2b;
    --silver: #b9b9b9;
  }
  * { box-sizing: border-box; margin: 0; padding: 0; }
  html, body {
    width: 1200px; height: 900px; overflow: hidden;
    background: var(--stage);
    font-family: "Work Sans", Arial, sans-serif;
    color: var(--ink);
  }
  .canvas { position: relative; width: 1200px; height: 900px; }
  .card {
    position: absolute; left: 310px; width: 580px; height: 332px;
    border-radius: 2px; box-shadow: 0 10px 30px rgba(0,0,0,.45);
  }

  /* front */
  .card-front {
    top: 70px;
    background: radial-gradient(ellipse at 60% 35%, #2c2c2c 0%, var(--card-dark) 70%);
    display: flex; align-items: center; justify-content: center; gap: 14px;
  }
  .brand-front { font-size: 54px; font-weight: 600; color: var(--silver); letter-spacing: 1px; }
  .mark-dot { width: 18px; height: 18px; border-radius: 50%; border: 2px solid var(--silver); }

  /* back */
  .card-back { top: 462px; background: var(--card-light); }
  .brand-back {
    position: absolute; right: 40px; top: 34px;
    display: flex; align-items: center; gap: 10px;
  }
  .brand-back .name { font-size: 44px; font-weight: 600; line-height: 52px; }
  .brand-back .mark-dot { border-color: var(--ink); width: 16px; height: 16px; }

  .field-label {
    font-size: 10px; font-weight: 600; letter-spacing: 1.8px;
    color: var(--muted); text-transform: uppercase;
  }
  .write-in { position: absolute; left: 40px; top: 40px; width: 250px; }
  .write-line { height: 30px; border-bottom: 1.5px solid var(--rule); }

  .schedule { position: absolute; left: 40px; top: 104px; }
  .days { display: flex; gap: 4px; margin-top: 6px; list-style: none; }
  .days li {
    width: 32px; height: 40px; border: 1px solid var(--rule);
    font-size: 10px; font-weight: 500; text-align: center; padding-top: 3px;
  }

  .rule { position: absolute; left: 40px; right: 40px; top: 176px; height: 1.5px; background: var(--rule); }

  .contact { position: absolute; left: 40px; top: 196px; list-style: none; }
  .contact li { display: flex; align-items: center; gap: 9px; font-size: 15px; line-height: 22px; }
  .contact svg { width: 10px; height: 10px; }

  .locations { position: absolute; right: 40px; top: 190px; list-style: none; }
  .locations .field-label { text-align: right; margin-bottom: 6px; }
  .location { display: flex; align-items: flex-start; justify-content: flex-end; gap: 10px; margin-bottom: 8px; }
  .location address { font-style: normal; text-align: right; font-size: 14px; line-height: 18px; }
  .check-box { width: 14px; height: 14px; border: 1.5px solid var(--ink); border-radius: 50%; margin-top: 2px; flex: none; }
</style>
</head>
<body>
<main class="canvas">
  <section class="card card-front" aria-label="Card front">
    <span class="brand-front">Morvin</span>
    <span class="mark-dot"></span>
  </section>

  <section class="card card-back" aria-label="Card back">
    <div class="brand-back"><span class="name">Morvin</span><span class="mark-dot"></span></div>

    <div class="write-in">
      <p class="field-label">Your server</p>
      <div class="write-line"></div>
    </div>

    <div class="schedule">
      <p class="field-label">My schedule</p>
      <ul class="days">
        <li>MON</li><li>TUE</li><li>WED</li><li>THU</li><li>FRI</li><li>SAT</li><li>SUN</li>
      </ul>
    </div>

    <div class="rule"></div>

    <ul class="contact">
      <li><svg viewBox="0 0 10 10"><path d="M2 1 L4 1 L4.6 3 L3.4 3.8 Q4.6 6 6.2 6.6 L7 5.4 L9 6 L9 8 Q5 9 1.4 4.2 Q1 2.4 2 1Z" fill="#1c1c1c"/></svg>(514) 730-4182</li>
      <li><svg viewBox="0 0 10 10"><rect x="0.5" y="2" width="9" height="6" fill="none" stroke="#1c1c1c"/><path d="M0.5 2 L5 5.5 L9.5 2" fill="none" stroke="#1c1c1c"/></svg>info@morvin.com</li>
      <li><svg viewBox="0 0 10 10"><circle cx="5" cy="5" r="4.3" fill="none" stroke="#1c1c1c"/><ellipse cx="5" cy="5" rx="1.8" ry="4.3" fill="none" stroke="#1c1c1c"/><path d="M0.7 5 H9.3" stroke="#1c1c1c"/></svg>www.morvin.com</li>
    </ul>

    <div class="locations">
      <p class="field-label">Circle your bar</p>
      <div class="location">
        <address>218b Harlow Street,<br>Ashmere, NZ, 8042</address>
        <span class="check-box"></span>
      </div>
      <div class="location">
        <address>2615 W Calder Ridge Rd<br>702-418-9053</address>
        <span class="check-box"></span>
      </div>
    </div>
  </section>
</main>
</body>
</html>
```